Real estate broker business card

Want a modern celan but effective business card for my residential and commercial real estate business. I want the back of the card to advertise my services and to capture business. I have attached the back of my current business card fore ideas
Updates

Logos, photo and text updates added! Added Saturday, September 3, 2016

Project Deadline Extended Reason: LOGOS, PHOTOS AND TEST JUST UPLOADED! I'M READY TO PICK A DESIGN! THANK YOU! Added Saturday, September 3, 2016

Target Market(s)

home buyers and seller. commercial buyers and sellers

Industry/Entity Type

Real Estate

Contact Information for Business Card

must have my contact information and my photo

Requirements
Must have
• Carla Ventrino
• Owner & Qualifying Broker
• Ventrino Real Estate Services
• 505.718.2094
• carla@ventrinohomes.example
• www.ventrinohomes.example
Nice to have
• metallic
• Business capture text: " Don't buy or lease property without someone looking out for your best interests. I will represent you on your home or investment purchase for FREE!"
• "Home owners, call today to receive a FREE market analysis for your homes value!

```html
<!DOCTYPE html>
<html lang="en">
<head>
<meta charset="UTF-8">
<title>Ventrino Real Estate Services – Business Card</title>
<link rel="stylesheet" href="https://fonts.googleapis.com/css2?family=Dosis:wght@400;500;600&display=swap">
<style>
  :root {
    --teal: #1f8a99;
    --teal-dark: #146873;
    --ink: #5b6166;
    --ink-soft: #7d848a;
    --silver-light: #f4f5f6;
    --silver-mid: #dfe2e4;
    --silver-dark: #c5c9cc;
    --paper: #ffffff;
    --stage: #e9ebec;
  }
  * { box-sizing: border-box; margin: 0; padding: 0; }
  html, body {
    width: 1200px;
    height: 950px;
    overflow: hidden;
    background: var(--stage);
    font-family: "Dosis", sans-serif;
  }
  .sheet {
    position: relative;
    width: 1200px;
    height: 950px;
  }
  .card {
    position: absolute;
    left: 240px;
    width: 720px;
    height: 412px;
    overflow: hidden;
    box-shadow: 0 6px 18px rgba(0,0,0,0.18);
  }

  /* ---------- Front: broker card ---------- */
  .card--broker {
    top: 38px;
    background: linear-gradient(160deg, var(--silver-light) 0%, var(--silver-mid) 60%, var(--silver-dark) 100%);
  }
  .broker-photo {
    position: absolute;
    left: 0;
    bottom: 56px;
    width: 330px;
    height: 250px;
    background: radial-gradient(ellipse at 45% 45%, #b89a8a 0%, #6a4a3e 45%, #d9d6d4 85%);
    border-top-right-radius: 140px;
  }
  .broker-details {
    position: absolute;
    right: 46px;
    top: 36px;
    width: 340px;
    text-align: center;
  }
  .brand {
    display: flex;
    align-items: center;
    justify-content: center;
    gap: 12px;
    margin-bottom: 26px;
  }
  .brand-dot {
    width: 34px;
    height: 34px;
    border-radius: 50%;
    background: var(--teal);
    flex: none;
  }
  .brand-name {
    color: var(--teal);
    font-weight: 600;
    font-size: 21px;
    letter-spacing: 2px;
    text-transform: uppercase;
    line-height: 1.1;
    text-align: left;
  }
  .broker-name {
    color: var(--teal);
    font-weight: 500;
    font-size: 30px;
    letter-spacing: 3px;
    text-transform: uppercase;
  }
  .broker-role {
    color: var(--ink);
    font-weight: 500;
    font-size: 17px;
    letter-spacing: 1.5px;
    text-transform: uppercase;
    line-height: 1.35;
    margin-top: 4px;
  }
  .contact-list {
    list-style: none;
    margin-top: 26px;
    text-align: right;
  }
  .contact-item {
    display: flex;
    align-items: center;
    justify-content: flex-end;
    gap: 10px;
    color: var(--ink);
    font-weight: 500;
    font-size: 17px;
    letter-spacing: 1px;
    text-transform: uppercase;
    line-height: 1.65;
  }
  .contact-icon {
    width: 18px;
    height: 18px;
    flex: none;
  }
  .offer-band {
    position: absolute;
    left: 0;
    right: 0;
    bottom: 0;
    height: 56px;
    background: linear-gradient(180deg, var(--teal) 0%, var(--teal-dark) 100%);
    color: var(--paper);
    font-weight: 600;
    font-size: 17px;
    letter-spacing: 1px;
    text-transform: uppercase;
    display: flex;
    align-items: center;
    justify-content: center;
  }

  /* ---------- Back: brand card ---------- */
  .card--brand {
    top: 500px;
    background: var(--paper);
    display: flex;
    align-items: center;
    justify-content: center;
  }
  .card--brand .brand {
    gap: 22px;
    margin: 0;
  }
  .card--brand .brand-dot {
    width: 96px;
    height: 96px;
  }
  .card--brand .brand-name {
    font-size: 40px;
    letter-spacing: 4px;
  }
</style>
</head>
<body>
<main class="sheet">

  <section class="card card--broker">
    <div class="broker-photo" role="img" aria-label="Portrait photo of Carla Ventrino"></div>

    <div class="broker-details">
      <div class="brand">
        <span class="brand-dot"></span>
        <span class="brand-name">Ventrino<br>Real Estate Services</span>
      </div>
      <h1 class="broker-name">Carla Ventrino</h1>
      <p class="broker-role">Owner &amp; Qualifying Broker<br>Ventrino Real Estate Services</p>

      <ul class="contact-list">
        <li class="contact-item">505.718.2094
          <svg class="contact-icon" viewBox="0 0 24 24" aria-hidden="true"><path fill="#1f8a99" d="M6.6 10.8a15.1 15.1 0 0 0 6.6 6.6l2.2-2.2a1 1 0 0 1 1-.25 11.4 11.4 0 0 0 3.6.57 1 1 0 0 1 1 1V20a1 1 0 0 1-1 1A17 17 0 0 1 3 4a1 1 0 0 1 1-1h3.5a1 1 0 0 1 1 1c0 1.25.2 2.45.57 3.57a1 1 0 0 1-.25 1z"/></svg>
        </li>
        <li class="contact-item" style="text-transform:none">carla@ventrinohomes.example
          <svg class="contact-icon" viewBox="0 0 24 24" aria-hidden="true"><rect x="2" y="5" width="20" height="14" rx="2" fill="#1f8a99"/><path d="M3 7l9 6 9-6" stroke="#fff" stroke-width="1.6" fill="none"/></svg>
        </li>
        <li class="contact-item" style="text-transform:none">www.ventrinohomes.example
          <svg class="contact-icon" viewBox="0 0 24 24" aria-hidden="true"><circle cx="12" cy="12" r="10" fill="#1f8a99"/><path d="M2 12h20M12 2c3 3 3 17 0 20M12 2c-3 3-3 17 0 20" stroke="#fff" stroke-width="1.3" fill="none"/></svg>
        </li>
      </ul>
    </div>

    <div class="offer-band">Home owners, call today to receive a free market analysis for your homes value!</div>
  </section>

  <section class="card card--brand">
    <div class="brand">
      <span class="brand-dot"></span>
      <span class="brand-name">Ventrino<br>Real Estate Services</span>
    </div>
  </section>

</main>
</body>
</html>
```